http://www.brindlewares.com/ New Ecommerce Site

We are redesigning Brindlewares.com on shopvantly.com.

We need to get a design for the ecommerce site.

They have about 15-45 products and these are the menu items that they need on the pages.

Knives:
Kitchen Knives
Neck Knives
Outdoor Knives
Bluefinch Knives
Clearance Knives
Premium Knives
Misc. Product:
Waterstones
Books
DVDs
T-Shirts
Scissors
Bladesmithing School
Videos
Links
Testimonials/Feedback
Contact Dennis Form
Knife Care and Maintenance Tips
Knife Sharpening
Knife Archives
Kitchen Knife Archives

We need several pages designed.

- Category Page
- Single Item page
- Knive Archive Pages (This is where old knives are stored that are not being sold anymore)
- Featured Product pages.
- Information pages
- checkout

The design has to be VERY elagant, like vostel.com.
And it has to be very easy to navigate and buy items like http://bladesgoquick.com/

Thanks,
Peter Hollis

Requirements
Must have
• Must be very elegant, and have the menu items somewhere on the pages.

```html
<!DOCTYPE html>
<html lang="en">
<head>
<meta charset="utf-8">
<title>Brindlewares</title>
<link href="https://fonts.googleapis.com/css2?family=Cinzel:wght@500&family=Open+Sans:wght@300;400;600;700&display=swap" rel="stylesheet">
<style>
:root{
  --header-bg:#141414;
  --nav-red:#b01e23;
  --nav-red-dark:#8c1419;
  --page-bg:#262626;
  --panel-black:#050505;
  --footer-bg:#2e2e2e;
  --accent-red:#c9343a;
  --text-light:#ffffff;
  --text-muted:#c8c8c8;
  --text-dim:#8a8a8a;
}
*{margin:0;padding:0;box-sizing:border-box}
html,body{width:681px;height:1200px;overflow:hidden;background:var(--page-bg);font-family:"Open Sans",sans-serif;color:var(--text-light)}
.canvas{position:relative;width:681px;height:1200px}
.abs{position:absolute}

.site-header{left:0;top:0;width:681px;height:77px;background:linear-gradient(#0e0e0e,#1d1d1d)}
.brand{left:0;width:640px;top:20px;text-align:center;font-family:"Cinzel",serif;font-size:26px;letter-spacing:1px;color:var(--text-light)}
.tagline{left:0;width:640px;top:51px;text-align:center;font-size:10px;color:var(--text-muted)}
.search{left:497px;top:47px;width:147px;height:20px;border:1px solid #444;background:#1a1a1a;font-size:7px;color:var(--text-dim);padding:5px 8px}
.search-btn{right:0;top:0;width:17px;height:18px;border-left:1px solid #444}

.main-nav{left:0;top:77px;width:681px;height:28px;background:linear-gradient(var(--nav-red),var(--nav-red-dark));border-top:1px solid #d4373c}
.nav-item{top:7px;font-size:10.5px;font-weight:600;transform:translateX(-50%);white-space:nowrap}
.nav-sep{top:0;width:1px;height:28px;background:#6e0f12;box-shadow:1px 0 0 #c9383d}

.hero{left:0;top:105px;width:681px;height:237px;background:linear-gradient(#262626,#1a1a1a)}
.hero-image{left:284px;top:3px;width:356px;height:232px;background:radial-gradient(ellipse at 55% 55%,#a8a8a8 0%,#6b4a2e 35%,#2a2a2a 75%);border-radius:4px}
.hero-kicker{left:54px;top:43px;font-size:19px;font-weight:300}
.hero-title{left:53px;top:65px;font-size:22px;font-weight:700}
.hero-copy{left:54px;top:98px;width:240px;font-size:7.5px;line-height:11px;color:var(--text-muted)}
.hero-btn{left:54px;top:129px;width:75px;height:22px;background:linear-gradient(#c82a30,#9e161b);border-radius:2px;font-size:7.5px;text-align:center;line-height:22px}
.dot{top:166px;width:6px;height:6px;border-radius:50%;background:#555}
.dot.active{background:#fff}

.sidebar{left:34px;top:366px;width:160px;height:349px;background:var(--panel-black);border:1px solid #333}
.sidebar-title{left:19px;top:11px;font-size:17px;color:var(--accent-red)}
.cat-list{left:23px;top:40px;width:114px;list-style:none}
.cat-list li{height:21px;border-bottom:1px solid #252525;font-size:8.5px;line-height:19px;padding-left:10px;position:relative}
.cat-list li::before{content:"";position:absolute;left:0;top:6px;border-left:4px solid #888;border-top:3.5px solid transparent;border-bottom:3.5px solid transparent}
.cat-list li:last-child{border-bottom:none}

.promo-image{left:34px;top:723px;width:158px;height:92px;background:linear-gradient(135deg,#e8eaec,#5a4a44 55%,#dadde0)}
.promo{left:34px;top:815px;width:158px;height:94px;background:var(--nav-red);padding:11px 15px}
.promo h3{font-size:11.5px;font-weight:600;margin-bottom:4px}
.promo p{font-size:7.5px;line-height:13px;color:#f3d6d7}

.section-title{left:211px;font-size:17px;font-weight:400}
.welcome-copy{left:212px;top:390px;width:434px;font-size:7.3px;line-height:16.2px;color:var(--text-muted)}

.product{width:133px}
.product-image{width:133px;height:97px;background:linear-gradient(160deg,#ffffff,#d9d9d9 60%,#b4b4b4)}
.product-image.dark{background:linear-gradient(160deg,#111,#4a3524 60%,#222)}
.product-image.rust{background:linear-gradient(160deg,#b55a3a,#a04a2e 60%,#cfcfcf)}
.product-name{margin-top:5px;font-size:10px;color:var(--accent-red)}
.product-desc{font-size:7.5px;line-height:12px;color:var(--text-muted)}
.price{margin-top:4px;font-size:12px}
.price s{color:var(--text-dim);margin-right:6px}

.site-footer{left:0;top:1115px;width:681px;height:85px;background:var(--footer-bg)}
.footer-nav{left:0;top:19px;width:681px;text-align:center;font-size:11px;color:#e5e5e5;word-spacing:2px}
.footer-nav span{margin:0 8px;color:#bbb}
.copyright{left:0;top:45px;width:681px;text-align:center;font-size:7.5px;color:var(--text-muted)}
</style>
</head>
<body>
<div class="canvas">

  <header class="site-header abs">
    <div class="brand abs">BRINDLEWARES</div>
    <div class="tagline abs">Third Generation Takesora Bladesmith</div>
    <div class="search abs">Search here
      <div class="search-btn abs"><svg width="17" height="18"><path d="M7 6l3 3-3 3" fill="none" stroke="#aaa" stroke-width="1.2"/></svg></div>
    </div>
  </header>

  <nav class="main-nav abs">
    <div class="nav-item abs" style="left:106px">Home</div>
    <div class="nav-sep abs" style="left:146px"></div>
    <div class="nav-item abs" style="left:188px">Knives</div>
    <div class="nav-sep abs" style="left:230px"></div>
    <div class="nav-item abs" style="left:268px">Tools</div>
    <div class="nav-sep abs" style="left:307px"></div>
    <div class="nav-item abs" style="left:358px">Instruction</div>
    <div class="nav-sep abs" style="left:407px"></div>
    <div class="nav-item abs" style="left:450px">About</div>
    <div class="nav-sep abs" style="left:491px"></div>
    <div class="nav-item abs" style="left:552px">Contact Dennis</div>
  </nav>

  <section class="hero abs">
    <div class="hero-image abs" role="img" aria-label="Large bowie knife with stag handle in front of a tooled leather sheath"></div>
    <div class="hero-kicker abs">Mauris vel lacus vitae</div>
    <div class="hero-title abs">Felis Vestibulum Volutpat</div>
    <p class="hero-copy abs">Mauris vel lacus vitae felis vestibulum volutpat. Etiam est nunc, venenatis in, tristique eu, imperdiet ac, nisl.</p>
    <div class="hero-btn abs">VIEW MORE</div>
    <div class="dot active abs" style="left:55px"></div>
    <div class="dot abs" style="left:64px"></div>
    <div class="dot abs" style="left:73px"></div>
    <div class="dot abs" style="left:82px"></div>
  </section>

  <aside class="sidebar abs">
    <div class="sidebar-title abs">Our Product</div>
    <ul class="cat-list abs">
      <li>KITCHEN KNIVES</li><li>NECK KNIVES</li><li>OUTDOOR KNIVES</li><li>BLUEFINCH KNIVES</li>
      <li>CLEARANCE KNIVES</li><li>PREMIUM KNIVES</li><li>MISC. PRODUCT:</li><li>WATERSTONES</li>
      <li>BOOKS</li><li>DVDS</li><li>T-SHIRTS</li><li>SCISSORS</li><li>BLADESMITHING SCHOOL</li><li>VIDEOS</li>
    </ul>
  </aside>

  <div class="promo-image abs" role="img" aria-label="Utility knife with wooden handle beside a black clip sheath"></div>
  <div class="promo abs">
    <h3>Bluefinch Series</h3>
    <p>An easily-concealable utility knife carried inside the belt in a clip Veltrex sheath. Original 10" long, Junior version 9", Compact version 8"</p>
  </div>

  <h2 class="section-title abs" style="top:366px">Welcome to Brindlewares Mainpage</h2>
  <p class="welcome-copy abs">Welcome to Brindlewares, your source of high performance hand-forged cutlery and practical sharpening instruction! I am Dennis Brindle, third generation Takesora Bladesmith and certified master bladesmith. You will benefit from my many years of knife making experience. I trained in a small mountain forge for over a decade, learning traditional methods from the smiths who came before me and earning my place in the Takesora line.<br>I have personally made thousands of knives and hand sharpened many more blades of all shapes and sizes. I am confident that you will experience the meaning of sharp like never before!</p>

  <h2 class="section-title abs" style="top:509px;left:213px">Latest Products</h2>

  <div class="product abs" style="left:214px;top:537px"><div class="product-image" role="img" aria-label="Hunting knife with brass guard"></div><div class="product-name">Product Name</div><div class="product-desc">Curabitur metus ipsum luctus eu malesuada ut tincidunt sed</div><div class="price"><s>$25.99</s>$21.99</div></div>
  <div class="product abs" style="left:362px;top:537px"><div class="product-image" role="img" aria-label="Chef knife with black handle"></div><div class="product-name">Product Name</div><div class="product-desc">Curabitur metus ipsum luctus eu malesuada ut tincidunt sed</div><div class="price"><s>$25.99</s>$21.99</div></div>
  <div class="product abs" style="left:511px;top:537px"><div class="product-image" role="img" aria-label="Kitchen knife with black handle"></div><div class="product-name">Product Name</div><div class="product-desc">Curabitur metus ipsum luctus eu malesuada ut tincidunt sed</div><div class="price"><s>$25.99</s>$21.99</div></div>

  <div class="product abs" style="left:214px;top:722px"><div class="product-image" role="img" aria-label="Dive knife with black sheath"></div><div class="product-name">Product Name</div><div class="product-desc">Curabitur metus ipsum luctus eu malesuada ut tincidunt sed</div><div class="price"><s>$25.99</s>$21.99</div></div>
  <div class="product abs" style="left:362px;top:722px"><div class="product-image" role="img" aria-label="Knife with wooden handle"></div><div class="product-name">Product Name</div><div class="product-desc">Curabitur metus ipsum luctus eu malesuada ut tincidunt sed</div><div class="price"><s>$25.99</s>$21.99</div></div>
  <div class="product abs" style="left:511px;top:722px"><div class="product-image" role="img" aria-label="Bowie knife with wooden handle"></div><div class="product-name">Product Name</div><div class="product-desc">Curabitur metus ipsum luctus eu malesuada ut tincidunt sed</div><div class="price"><s>$25.99</s>$21.99</div></div>

  <div class="product abs" style="left:215px;top:900px"><div class="product-image dark" role="img" aria-label="Outdoor knife with leather sheath"></div><div class="product-name">Product Name</div><div class="product-desc">Curabitur metus ipsum luctus eu malesuada ut tincidunt sed</div><div class="price"><s>$25.99</s>$21.99</div></div>
  <div class="product abs" style="left:363px;top:900px"><div class="product-image" role="img" aria-label="Knife with stacked leather handle"></div><div class="product-name">Product Name</div><div class="product-desc">Curabitur metus ipsum luctus eu malesuada ut tincidunt sed</div><div class="price"><s>$25.99</s>$21.99</div></div>
  <div class="product abs" style="left:512px;top:900px"><div class="product-image rust" role="img" aria-label="Knife on rust-coloured leather"></div><div class="product-name">Product Name</div><div class="product-desc">Curabitur metus ipsum luctus eu malesuada ut tincidunt sed</div><div class="price"><s>$25.99</s>$21.99</div></div>

  <footer class="site-footer abs">
    <div class="footer-nav abs">Home<span>|</span>Knives<span>|</span>Tools<span>|</span>Instruction<span>|</span>About<span>|</span>Contact Dennis</div>
    <div class="copyright abs">Copyright © 2013 Company Name. &nbsp;All right reserved. &nbsp;Term of Use</div>
  </footer>

</div>
</body>
</html>
```